TA BRAMLEY BUSINESS CARD DESIGN PROJECT

We need to utilize our logo that was expertly created on PixelHarbor and now need to match this with a business card design.

```html
<!DOCTYPE html>
<html lang="en">
<head>
<meta charset="utf-8">
<title>TA BRAMLEY Business Card</title>
<link rel="stylesheet" href="https://fonts.googleapis.com/css2?family=Open+Sans:wght@400;600;700;800&display=swap">
<style>
  :root {
    --stage: #232323;
    --card: #ffffff;
    --brand-blue: #1656a6;
    --ink: #1a1a1a;
    --rule: #111111;
  }
  * { margin: 0; padding: 0; box-sizing: border-box; }
  html, body { width: 1200px; height: 780px; overflow: hidden; }
  body {
    background: var(--stage);
    font-family: "Open Sans", Arial, sans-serif;
    position: relative;
  }
  .card {
    position: absolute;
    left: 305px;
    width: 590px;
    height: 337px;
    background: var(--card);
    overflow: hidden;
  }
  .card--front { top: 38px; }
  .card--back { top: 405px; }

  .edge-bar {
    position: absolute;
    width: 12px;
    background: var(--brand-blue);
  }
  .edge-bar--left { left: 0; top: 150px; height: 145px; }
  .edge-bar--right { right: 0; top: 40px; height: 130px; }

  .wordmark {
    display: flex;
    align-items: center;
    gap: 12px;
    color: var(--brand-blue);
    font-weight: 800;
    letter-spacing: 0.08em;
    white-space: nowrap;
  }
  .wordmark__square {
    background: var(--brand-blue);
    flex: none;
  }
  .card--front .wordmark {
    position: absolute;
    left: 50%;
    top: 50%;
    transform: translate(-50%, -50%);
    font-size: 46px;
  }
  .card--front .wordmark__square { width: 34px; height: 34px; }

  .card--back .wordmark {
    position: absolute;
    left: 48px;
    top: 128px;
    font-size: 27px;
  }
  .card--back .wordmark__square { width: 20px; height: 20px; }

  .divider {
    position: absolute;
    left: 300px;
    top: 40px;
    width: 1px;
    height: 200px;
    background: var(--rule);
  }

  .contact {
    position: absolute;
    left: 326px;
    top: 44px;
    color: var(--ink);
  }
  .contact__name {
    color: var(--brand-blue);
    font-weight: 700;
    font-size: 25px;
    line-height: 1.1;
  }
  .contact__role {
    font-weight: 600;
    font-size: 13px;
    margin-top: 2px;
  }
  .contact__list {
    list-style: none;
    margin-top: 22px;
    font-size: 14px;
    line-height: 1.55;
  }
  .contact__list li { display: flex; align-items: center; gap: 9px; }
  .contact__icon { width: 14px; height: 14px; flex: none; }

  .address {
    position: absolute;
    left: 0;
    right: 0;
    bottom: 60px;
    text-align: center;
    font-size: 15px;
    color: var(--ink);
  }
</style>
</head>
<body>

<section class="card card--front" aria-label="Business card front">
  <span class="edge-bar edge-bar--left"></span>
  <span class="edge-bar edge-bar--right"></span>
  <div class="wordmark"><span class="wordmark__square"></span>TA BRAMLEY</div>
</section>

<section class="card card--back" aria-label="Business card back">
  <span class="edge-bar edge-bar--left"></span>
  <span class="edge-bar edge-bar--right"></span>
  <div class="wordmark"><span class="wordmark__square"></span>TA BRAMLEY</div>
  <span class="divider"></span>

  <div class="contact">
    <p class="contact__name">Lena Vostrova</p>
    <p class="contact__role">Managing Director</p>
    <ul class="contact__list">
      <li>
        <svg class="contact__icon" viewBox="0 0 16 16" aria-hidden="true">
          <path fill="#1656a6" d="M3.6 1.5l2.3 2.6-1.3 1.6c.9 2 2.4 3.5 4.4 4.4l1.6-1.3 2.6 2.3-1.4 2.3C6.9 13.2 2.8 9.1 1.3 3l2.3-1.5z"/>
        </svg>
        (555) 214-3068
      </li>
      <li>
        <svg class="contact__icon" viewBox="0 0 16 16" aria-hidden="true">
          <rect x="1" y="3" width="14" height="10" rx="1.5" fill="#1656a6"/>
          <path d="M1.8 4l6.2 4.8L14.2 4" fill="none" stroke="#fff" stroke-width="1.3"/>
        </svg>
        hello@tabramley.com
      </li>
      <li>
        <svg class="contact__icon" viewBox="0 0 16 16" aria-hidden="true">
          <circle cx="8" cy="8" r="7" fill="#1656a6"/>
          <path d="M1 8h14M8 1c-2.6 2.8-2.6 11.2 0 14M8 1c2.6 2.8 2.6 11.2 0 14" fill="none" stroke="#fff" stroke-width="1"/>
        </svg>
        www.tabramley.com
      </li>
    </ul>
  </div>

  <p class="address">418 Harlow Ave Dallas, Texas 75201 USA</p>
</section>

</body>
</html>
```